Trabworth Business Cards

We need a business card design for Trabworth Mining.

This is a B2B company that buys and sells large machinery tires within the coal mining industry. The design should the strong, crisp and masculine. I have uploaded the company logo and rough mock-up of what the back of the card should look like. the front of the card should have the same look/feel as the back. I need editable templates for both the front and the back of the card.

Color scheme should be grey/green/black

Contact information to include on the card:
Name: Dale Pembrose
Title: Managing Director
Phone: 555-314-2069
Address: 1187 Welford #3 Dallas, TX 75290
Email: Dale@Trabworth-example.com

I am also opening a contest for letterhead design. If you submit a business card design, please also submit a letterhead design with the same look/feel. The winner of the business card design will also will the letter head and be paid for both.

Target Market(s)

Procurement men/women in the coal mining industry

Industry/Entity Type

Coal Mining

```html
<!DOCTYPE html>
<html lang="en">
<head>
<meta charset="utf-8">
<title>Trabworth Business Cards</title>
<link rel="stylesheet" href="https://fonts.googleapis.com/css2?family=Ubuntu:wght@400;500;700&display=swap">
<style>
  :root {
    --backdrop: #a9673f;
    --card-white: #fbfbfb;
    --card-dark: #2e2f30;
    --card-dark-tone: #353637;
    --brand-green: #5fb33a;
    --brand-grey: #5c5d5f;
    --text-light: #f2f2f2;
  }
  * { margin: 0; padding: 0; box-sizing: border-box; }
  html, body {
    width: 1200px; height: 900px; overflow: hidden;
    background: var(--backdrop);
    font-family: "Ubuntu", sans-serif;
  }
  .canvas { position: relative; width: 1200px; height: 900px; }

  .card {
    position: absolute; left: 354px; width: 488px; height: 278px;
    overflow: hidden;
    box-shadow: 0 2px 6px rgba(0,0,0,0.35);
  }
  .card--front { top: 162px; background: var(--card-white); }
  .card--back { top: 471px; background: var(--card-dark); }

  .wordmark {
    position: absolute; display: flex; align-items: center; gap: 10px;
    font-weight: 500; font-size: 30px; letter-spacing: 0.5px; white-space: nowrap;
  }
  .wordmark__square { width: 14px; height: 14px; background: var(--brand-green); flex: none; }
  .card--front .wordmark { left: 36px; top: 50px; color: var(--brand-grey); }
  .card--back .wordmark { right: 32px; top: 172px; color: var(--text-light); }

  .contact-band {
    position: absolute; left: 0; top: 147px; width: 100%; height: 115px;
    background: linear-gradient(90deg, var(--card-dark) 0%, var(--card-dark-tone) 100%);
  }
  .contact-band__pattern {
    position: absolute; inset: 0;
    background: linear-gradient(90deg, rgba(255,255,255,0) 20%, rgba(255,255,255,0.03) 100%);
  }
  .person {
    position: absolute; left: 38px; top: 10px;
    display: flex; align-items: center; color: var(--text-light);
  }
  .person__dot { width: 7px; height: 7px; border-radius: 50%; background: var(--brand-green); margin-right: 22px; }
  .person__name { font-size: 16px; }
  .person__title { font-size: 11.5px; text-transform: uppercase; margin-left: 4px; padding-left: 5px; border-left: 1px solid var(--text-light); line-height: 12px; }

  .contact-list { position: absolute; left: 36px; top: 43px; list-style: none; }
  .contact-list li {
    display: flex; align-items: center; height: 21px;
    font-size: 14px; color: var(--text-light);
  }
  .contact-list svg { width: 12px; height: 12px; margin-right: 19px; fill: var(--brand-green); }

  .back-pattern {
    position: absolute; inset: 0;
    background: radial-gradient(ellipse at 30% 20%, rgba(255,255,255,0.04), rgba(255,255,255,0) 70%);
  }
  .website {
    position: absolute; right: 32px; top: 222px;
    font-size: 14px; letter-spacing: 1px; color: var(--text-light);
  }
</style>
</head>
<body>
<main class="canvas">

  <section class="card card--front" aria-label="Business card front">
    <div class="wordmark"><span class="wordmark__square"></span>Trabworth Mining</div>

    <div class="contact-band">
      <div class="contact-band__pattern" role="img" aria-label="Subtle dark hexagon texture"></div>
      <div class="person">
        <span class="person__dot"></span>
        <span class="person__name">Dale Pembrose</span>
        <span class="person__title">Managing Director</span>
      </div>
      <ul class="contact-list">
        <li>
          <svg viewBox="0 0 24 24" aria-hidden="true"><path d="M6.6 10.8a15 15 0 0 0 6.6 6.6l2.2-2.2a1 1 0 0 1 1-.25 11.4 11.4 0 0 0 3.6.57 1 1 0 0 1 1 1V20a1 1 0 0 1-1 1A17 17 0 0 1 3 4a1 1 0 0 1 1-1h3.5a1 1 0 0 1 1 1c0 1.25.2 2.45.57 3.57a1 1 0 0 1-.25 1z"/></svg>
          555-314-2069
        </li>
        <li>
          <svg viewBox="0 0 24 24" aria-hidden="true"><path d="M2 5h20v14H2zm2 2v.5l8 5 8-5V7zm0 2.9V17h16V9.9l-8 5z"/></svg>
          Dale@Trabworth-example.com
        </li>
        <li>
          <svg viewBox="0 0 24 24" aria-hidden="true"><path d="M12 2a7 7 0 0 0-7 7c0 5 7 13 7 13s7-8 7-13a7 7 0 0 0-7-7zm0 9.5A2.5 2.5 0 1 1 12 6.5a2.5 2.5 0 0 1 0 5z"/></svg>
          1187 Welford #3 Dallas, TX 75290
        </li>
      </ul>
    </div>
  </section>

  <section class="card card--back" aria-label="Business card back">
    <div class="back-pattern" role="img" aria-label="Subtle dark hexagon texture"></div>
    <div class="wordmark"><span class="wordmark__square"></span>Trabworth Mining</div>
    <p class="website">www.Trabworth-example.com</p>
  </section>

</main>
</body>
</html>
```